Brovanek Data Yellow rose letterhead

I have a new logo for my company but in its current form it is too large to be used on letterhead or as a email signature. I need to have the designer use elements from the current logo and create something close to the original but more suited for smaller items.
Updates

I just uploaded a copy of our logo that does not have the weathered affect. Thanks

Reason: More time for revisions

Industry/Entity Type

It Company

Requirements
Must have
• The design must maintain the visual effect of the current logo. It needs to include the yellow rose and the name of the company.
Nice to have
• It would be nice to maintain the stamp theme and incorporate my name, address, phone, email. etc.

```html
<!DOCTYPE html>
<html lang="en">
<head>
<meta charset="utf-8">
<title>Brovanek Data Letterhead</title>
<link href="https://fonts.googleapis.com/css2?family=Arimo:wght@400;700&display=swap" rel="stylesheet">
<style>
  :root {
    --backdrop: #bdbdbd;
    --paper: #ffffff;
    --ink: #3b302b;
    --brand-brown: #4d423b;
    --rose-yellow: #f7c21c;
    --band-yellow-light: #ffdf6e;
    --band-yellow: #f9c308;
  }
  * { box-sizing: border-box; margin: 0; padding: 0; }
  html, body {
    width: 848px;
    height: 1200px;
    overflow: hidden;
    background: var(--backdrop);
    font-family: "Arimo", Arial, sans-serif;
  }
  .letterhead {
    position: absolute;
    left: 110px;
    top: 155px;
    width: 628px;
    height: 890px;
    background: var(--paper);
    overflow: hidden;
    box-shadow: 0 18px 40px rgba(0, 0, 0, 0.35);
  }
  .brand {
    position: absolute;
    top: 16px;
    left: 0;
    width: 100%;
    display: flex;
    flex-direction: column;
    align-items: center;
    padding-left: 22px;
  }
  .brand-mark {
    width: 86px;
    height: 86px;
    border-radius: 50%;
    background: var(--rose-yellow);
  }
  .brand-name {
    margin-top: 16px;
    font-weight: 700;
    font-size: 25px;
    letter-spacing: 1.5px;
    text-transform: uppercase;
    color: var(--brand-brown);
    line-height: 1;
    white-space: nowrap;
  }
  .contact {
    position: absolute;
    left: 22px;
    top: 740px;
    font-size: 13.5px;
    line-height: 18px;
    color: var(--ink);
    font-style: normal;
  }
  .footer-band {
    position: absolute;
    left: 0;
    bottom: 0;
    width: 628px;
    height: 50px;
    background: linear-gradient(to bottom, var(--band-yellow-light), var(--band-yellow));
  }
</style>
</head>
<body>
  <main class="letterhead">
    <header class="brand">
      <div class="brand-mark" aria-hidden="true"></div>
      <div class="brand-name">Brovanek Data</div>
    </header>

    <address class="contact">
      Mara Ellison, PhD<br>
      740 NE Cedar Ridge Road, Ste 2104<br>
      Mill Creek, TX 76510<br>
      mara@brovanek-data.com<br>
      1-800-555-0147
    </address>

    <div class="footer-band" role="img" aria-label="Yellow footer band with a brown scalloped stamp-edge border"></div>
  </main>
</body>
</html>
```